business card design for a plumbing contractor

i need a double business card for a plumbing business, our initial service is residential Sewer Drain Cleaning.

Target Market(s)

other plumbing Business

Industry/Entity Type

Plumbing

Contact Information for Business Card

www.PipeworksTopMark.example- 5307218394-

Font styles to use
Serif

Colors
ec1f27
0455a3

```html
<!DOCTYPE html>
<html lang="en">
<head>
<meta charset="utf-8">
<title>Pipeworks TopMark – Business Card</title>
<link rel="stylesheet" href="https://fonts.googleapis.com/css2?family=Roboto+Condensed:wght@400;700&family=Roboto:wght@400;500&display=swap">
<style>
  :root {
    --brand-red: #d9332e;
    --brand-red-dark: #c42a26;
    --ink-grey: #7d7b74;
    --text-grey: #55534f;
    --card-white: #fbfbfa;
    --stage: #e9e7e3;
  }
  * { margin: 0; padding: 0; box-sizing: border-box; }
  html, body { width: 1200px; height: 886px; overflow: hidden; }
  body {
    background: var(--stage);
    font-family: "Roboto", Arial, sans-serif;
    display: flex;
    align-items: center;
    justify-content: center;
    gap: 40px;
  }
  .card {
    position: relative;
    width: 540px;
    height: 309px;
    border-radius: 16px;
    overflow: hidden;
    box-shadow: 0 6px 18px rgba(0,0,0,0.18);
  }

  /* Front */
  .card--front { background: var(--card-white); }
  .front__brand {
    position: absolute;
    top: 44px;
    right: 44px;
    display: flex;
    align-items: center;
    gap: 10px;
  }
  .front__brand-name {
    font-family: "Roboto Condensed", Arial, sans-serif;
    font-weight: 700;
    font-size: 30px;
    line-height: 1;
    color: var(--ink-grey);
  }
  .brand-square {
    width: 22px;
    height: 22px;
    background: var(--brand-red);
  }
  .front__contact {
    position: absolute;
    left: 30px;
    bottom: 62px;
  }
  .contact__name {
    font-family: "Roboto Condensed", Arial, sans-serif;
    font-weight: 700;
    font-size: 20px;
    color: var(--brand-red);
    letter-spacing: 0.3px;
  }
  .contact__title {
    font-family: "Roboto Condensed", Arial, sans-serif;
    font-size: 14px;
    color: var(--ink-grey);
    margin-bottom: 10px;
  }
  .contact__list { list-style: none; }
  .contact__item {
    display: flex;
    align-items: center;
    gap: 8px;
    font-size: 12px;
    line-height: 19px;
    color: var(--text-grey);
  }
  .contact__icon { width: 11px; height: 11px; fill: var(--brand-red); flex: none; }
  .front__band {
    position: absolute;
    left: 0; right: 0; bottom: 0;
    height: 40px;
    background: var(--brand-red);
    display: flex;
    align-items: center;
    padding-left: 30px;
  }
  .services {
    font-family: "Roboto", Arial, sans-serif;
    font-size: 13px;
    color: #fff;
    letter-spacing: 0.2px;
    white-space: nowrap;
  }

  /* Back */
  .card--back {
    background: linear-gradient(135deg, var(--brand-red) 0%, var(--brand-red-dark) 100%);
  }
  .back__services-strip {
    position: absolute;
    left: 10px;
    top: 0;
    bottom: 0;
    width: 20px;
    display: flex;
    align-items: center;
    justify-content: center;
  }
  .back__services {
    writing-mode: vertical-rl;
    font-size: 10px;
    letter-spacing: 0;
  }
  .back__brand {
    position: absolute;
    inset: 0;
    display: flex;
    align-items: center;
    justify-content: center;
    gap: 14px;
    padding-left: 20px;
  }
  .back__brand-name {
    font-family: "Roboto Condensed", Arial, sans-serif;
    font-weight: 700;
    font-size: 44px;
    line-height: 1;
    color: #fff;
  }
  .back__brand .brand-square { background: #fff; width: 30px; height: 30px; }
</style>
</head>
<body>
  <section class="card card--front" aria-label="Card front">
    <div class="front__brand">
      <span class="front__brand-name">Pipeworks TopMark</span>
      <span class="brand-square"></span>
    </div>

    <div class="front__contact">
      <p class="contact__name">DALE MERCER</p>
      <p class="contact__title">CEO/FOUNDER</p>
      <ul class="contact__list">
        <li class="contact__item">
          <svg class="contact__icon" viewBox="0 0 24 24" aria-hidden="true"><path d="M6.6 10.8a15 15 0 0 0 6.6 6.6l2.2-2.2c.3-.3.7-.4 1-.2 1.1.4 2.3.6 3.6.6.6 0 1 .4 1 1V20c0 .6-.4 1-1 1A17 17 0 0 1 3 4c0-.6.4-1 1-1h3.5c.6 0 1 .4 1 1 0 1.3.2 2.5.6 3.6.1.3 0 .7-.2 1z"/></svg>
          5307218394
        </li>
        <li class="contact__item">
          <svg class="contact__icon" viewBox="0 0 24 24" aria-hidden="true"><path d="M2 5h20v14H2zm2 2v.5l8 5 8-5V7z"/></svg>
          Dispatcher@PipeworksTopMark.example
        </li>
        <li class="contact__item">
          <svg class="contact__icon" viewBox="0 0 24 24" aria-hidden="true"><circle cx="12" cy="12" r="10"/></svg>
          www.PipeworksTopMark.example
        </li>
      </ul>
    </div>

    <div class="front__band">
      <p class="services">Sewer Drain Cleaning • Maintenance • Trenchless Pipe Installs</p>
    </div>
  </section>

  <section class="card card--back" aria-label="Card back">
    <div class="back__services-strip">
      <p class="services back__services">Sewer Drain Cleaning • Maintenance • Trenchless Pipe Installs</p>
    </div>
    <div class="back__brand">
      <span class="back__brand-name">Pipeworks TopMark</span>
      <span class="brand-square"></span>
    </div>
  </section>
</body>
</html>
```